tinyTally Resource Book - 10 maths tasks to do outside

I need a 22 (11 pages back to back) page A6 sized book produced to standard for submission to professional printer. Needs to be as .pdf file showing guide lines and allowances for colour bleed. I have text already written and submitted as attachment in a Word file with margins set to A6 size. The theme of the materials is "Nature Play" so using lots of pictures from nature (Australia preferably) and showing lots of patterns in nature (rocks, leaves, flower petals etc). Some of the tasks refer to specific activities, such as "shadows" and "floating" so would be great to illustrate appropriately. The big emphasis is on learning outside the classroom, getting kids to engage actively with nature. I would like to see the pages as full colour - so not white background. The book itself will be spiral bound along the top edge so a margin of at least 1cm will be required at the top of each page (or the bottom of even numbered pages). Book will be printed on plastic laminated matte paper for outdoor use. Font size needs to be big enough to read. Fonts sizes, alignments and page numbers are all different at the moment and need to be standardised. One photo is included in a page as a sample if you can use it, otherwise disregard. Logo for Wattlebrook Numeracy Guild is also included to have as part of the acknowledgements at the back of the book.

Target Market(s)

Book is for early childhood and preschool teachers.

Industry/Entity Type

Education

Font styles to use
Sans Serif

Requirements
Must have
• Colour and appeal.
Nice to have
• Use of natural colours instead of bright catchy colours but that is your call.
Should not have
• American spelling

```html
<!DOCTYPE html>
<html lang="en-AU">
<head>
<meta charset="utf-8">
<title>Thanks – tinyTally Resource Book</title>
<link rel="stylesheet" href="https://fonts.googleapis.com/css2?family=Nunito:wght@900&family=Questrial&display=swap">
<style>
  :root {
    --paper: #ffffff;
    --crop-line: #222222;
    --panel-top: #c9cbe6;
    --panel-mid: #bfc4e3;
    --panel-light: #dfe6f5;
    --panel-pink: #d7c2df;
    --title-navy: #263b8c;
    --body-ink: #1e1e24;
  }
  html, body {
    margin: 0;
    padding: 0;
    overflow: hidden;
    background: var(--paper);
  }
  .page {
    position: relative;
    width: 892px;
    height: 1200px;
    overflow: hidden;
    background: var(--paper);
  }
  .crop-marks {
    position: absolute;
    inset: 0;
  }
  .bleed-panel {
    position: absolute;
    left: 53px;
    top: 53px;
    width: 786px;
    height: 1094px;
    background:
      radial-gradient(ellipse at 80% 55%, var(--panel-light) 0%, transparent 45%),
      radial-gradient(ellipse at 15% 85%, var(--panel-pink) 0%, transparent 40%),
      linear-gradient(170deg, var(--panel-top) 0%, var(--panel-mid) 50%, var(--panel-top) 100%);
  }
  .content {
    position: absolute;
    left: 124px;
    top: 96px;
    width: 643px;
    color: var(--body-ink);
  }
  .page-title {
    margin: 0 0 14px;
    font-family: "Nunito", sans-serif;
    font-weight: 900;
    font-size: 44px;
    line-height: 1.2;
    text-align: center;
    color: var(--title-navy);
    letter-spacing: 0.5px;
  }
  .acknowledgement {
    margin: 0 0 13px;
    font-family: "Questrial", sans-serif;
    font-size: 28px;
    line-height: 43.5px;
    text-align: justify;
  }
</style>
</head>
<body>
<div class="page">
  <div class="bleed-panel" role="img" aria-label="Decorative background of overlapping rounded line loops in soft blue, pink and white"></div>

  <svg class="crop-marks" width="892" height="1200" viewBox="0 0 892 1200" aria-hidden="true">
    <g stroke="var(--crop-line)" stroke-width="1" fill="none">
      <line x1="0" y1="53" x2="40" y2="53"/><line x1="53" y1="0" x2="53" y2="40"/>
      <line x1="852" y1="53" x2="892" y2="53"/><line x1="839" y1="0" x2="839" y2="40"/>
      <line x1="0" y1="1147" x2="40" y2="1147"/><line x1="53" y1="1160" x2="53" y2="1200"/>
      <line x1="852" y1="1147" x2="892" y2="1147"/><line x1="839" y1="1160" x2="839" y2="1200"/>
    </g>
  </svg>

  <main class="content">
    <h1 class="page-title">Thanks</h1>
    <p class="acknowledgement">I would like to acknowledge the Ngunnawal people, the tradition custodians of the land and carers for the magnificent environment in which Canberra is located and through which we are engaging in this project.</p>
    <p class="acknowledgement">I would like to acknowledge the support of the Riverbend Council Outdoor Learning Grant Program and the Wattlebrook Numeracy Guild in the production of this resource.</p>
    <p class="acknowledgement">I would also like to thank the following people who contributed to the ideas and development of the resource:</p>
    <p class="acknowledgement">Nadia Corwin, Rochelle Finlay, Emmeline Grant, Alex Holloway, Jenna Lockwood, Tessa Lowe, Molly Quinlan, Julia Renshaw, Marianne Redford, Leigh Whitcombe, Annie Walsh, Sally Winters</p>
    <p class="acknowledgement">Original artwork by Philip Tarrant, Bluewren Studio</p>
  </main>
</div>
</body>
</html>
```